Letterhead and matching envelope design for a dental office

We need a new stationary design, letterhead and envelope #10, for a dental office in Denver area. We are called Bright Harbor Dental. We want a simple and minimalistic design but not a boring design. I wish to have one good point that makes it look professional. I have attached our logo. Feel free to use either one. I want the design for letterhead and envelope look like a "matching pair" but not look the same. The envelope doesn't have to be white and it will have an address window on bottom left.

Target Market(s)

everyone who visits dentist (adults)

Industry/Entity Type

Dental

Font styles to use
Other font styles liked:
• close to font on logo or something that matches well

Requirements
Must have
• professional
• simple, minimalistic
• unique point that stands out
Nice to have
• matching but not same design for letterhead and envelope
Should not have
• not look like all the other boring designs
• no flowery, distracting feats

```html
<!DOCTYPE html>
<html lang="en">
<head>
<meta charset="utf-8">
<title>Bright Harbor Dental – Envelope #10, front and back</title>
<link rel="stylesheet" href="https://fonts.googleapis.com/css2?family=Cinzel:wght@600&family=PT+Sans:wght@400&display=swap">
<style>
  :root {
    --backdrop: #5fba5c;
    --paper: #ffffff;
    --paper-tint: #eef6f1;
    --brand-green: #2fa84a;
    --band-green: #27a045;
    --ink-grey: #5d6660;
    --line-grey: #c9d3cd;
    --flap-shadow: #e4e8e6;
  }
  * { box-sizing: border-box; margin: 0; padding: 0; }
  html, body { width: 1200px; height: 1200px; overflow: hidden; }
  body {
    background: var(--backdrop);
    font-family: "PT Sans", Arial, sans-serif;
    position: relative;
  }
  .envelope {
    position: absolute;
    left: 100px;
    width: 1000px;
    height: 434px;
    background: var(--paper);
    overflow: hidden;
  }
  .envelope--front {
    top: 70px;
    background: linear-gradient(160deg, var(--paper-tint) 0%, var(--paper) 45%, var(--paper) 100%);
  }
  .envelope--back { top: 600px; }

  /* Front: sender block */
  .sender { position: absolute; left: 48px; top: 38px; }
  .brand-name {
    font-family: "Cinzel", "Times New Roman", serif;
    font-weight: 600;
    font-size: 26px;
    letter-spacing: 2px;
    color: var(--brand-green);
    display: flex;
    align-items: center;
    gap: 12px;
  }
  .brand-dot {
    width: 14px; height: 14px;
    border-radius: 50%;
    background: var(--brand-green);
  }
  .brand-location {
    font-family: "Cinzel", "Times New Roman", serif;
    font-weight: 600;
    font-size: 12px;
    letter-spacing: 9px;
    color: var(--brand-green);
    margin: 4px 0 0 26px;
  }
  .sender-address {
    font-size: 12px;
    color: var(--ink-grey);
    margin-top: 8px;
  }

  /* Address window */
  .address-window {
    position: absolute;
    left: 48px;
    top: 150px;
    width: 330px;
    height: 180px;
    border: 1px solid var(--line-grey);
    border-radius: 22px;
    background: var(--paper);
  }

  /* Contact strip */
  .contact-strip {
    position: absolute;
    left: 0; right: 0; bottom: 0;
    height: 56px;
    display: flex;
    align-items: flex-start;
    gap: 70px;
    padding: 0 0 0 220px;
  }
  .contact-strip::after {
    content: "";
    position: absolute;
    left: 190px; right: 0; bottom: 0;
    height: 10px;
    background: var(--band-green);
  }
  .contact-item {
    display: flex;
    flex-direction: column;
    align-items: center;
    gap: 3px;
    font-size: 11px;
    color: var(--ink-grey);
  }
  .contact-icon { width: 14px; height: 14px; }

  /* Back */
  .flap { position: absolute; inset: 0; width: 100%; height: 100%; }
  .seal {
    position: absolute;
    left: 250px;
    top: 330px;
    display: flex;
    align-items: center;
    gap: 10px;
    font-family: "Cinzel", "Times New Roman", serif;
    font-weight: 600;
    font-size: 22px;
    letter-spacing: 2px;
    color: var(--brand-green);
  }
  .seal .brand-dot { width: 12px; height: 12px; }
</style>
</head>
<body>

<section class="envelope envelope--front" aria-label="Envelope front">
  <div class="sender">
    <div class="brand-name"><span class="brand-dot"></span>Bright Harbor Dental</div>
    <div class="brand-location">Lakewood</div>
    <div class="sender-address">000 Harbor View Rd, Suite 300, Denver, US 0000</div>
  </div>

  <div class="address-window" aria-label="Address window"></div>

  <div class="contact-strip">
    <div class="contact-item">
      <svg class="contact-icon" viewBox="0 0 14 14" aria-hidden="true">
        <circle cx="7" cy="7" r="6.3" fill="none" stroke="#2fa84a" stroke-width="1.2"/>
        <path d="M5 4.2c.5-.4 1-.3 1.2.2l.4.9c.1.3 0 .6-.3.8l-.3.2c.3.7.8 1.2 1.5 1.5l.2-.3c.2-.3.5-.4.8-.3l.9.4c.5.2.6.7.2 1.2-.5.6-1.3.7-2 .4C6 8.7 5.3 8 4.7 6.6c-.3-.8-.2-1.8.3-2.4z" fill="#2fa84a"/>
      </svg>
      <span>000.999.0000</span>
    </div>
    <div class="contact-item">
      <svg class="contact-icon" viewBox="0 0 14 14" aria-hidden="true">
        <circle cx="7" cy="7" r="6.3" fill="none" stroke="#2fa84a" stroke-width="1.2"/>
        <rect x="4.5" y="3.6" width="5" height="2.4" fill="#2fa84a"/>
        <rect x="3.5" y="6.2" width="7" height="3" rx="0.6" fill="#2fa84a"/>
        <rect x="4.8" y="8.4" width="4.4" height="2" fill="#fff" stroke="#2fa84a" stroke-width="0.6"/>
      </svg>
      <span>000.441.0000</span>
    </div>
    <div class="contact-item">
      <svg class="contact-icon" viewBox="0 0 14 14" aria-hidden="true">
        <circle cx="7" cy="7" r="6.3" fill="none" stroke="#2fa84a" stroke-width="1.2"/>
        <rect x="3.6" y="4.8" width="6.8" height="4.6" fill="none" stroke="#2fa84a" stroke-width="0.9"/>
        <path d="M3.6 4.8 7 7.5l3.4-2.7" fill="none" stroke="#2fa84a" stroke-width="0.9"/>
      </svg>
      <span>example@example.com</span>
    </div>
    <div class="contact-item">
      <svg class="contact-icon" viewBox="0 0 14 14" aria-hidden="true">
        <circle cx="7" cy="7" r="6.3" fill="none" stroke="#2fa84a" stroke-width="1.2"/>
        <circle cx="7" cy="7" r="3.6" fill="none" stroke="#2fa84a" stroke-width="0.9"/>
        <path d="M3.4 7h7.2M7 3.4c-1.5 1.8-1.5 5.4 0 7.2M7 3.4c1.5 1.8 1.5 5.4 0 7.2" fill="none" stroke="#2fa84a" stroke-width="0.8"/>
      </svg>
      <span>www.example.com</span>
    </div>
  </div>
</section>

<section class="envelope envelope--back" aria-label="Envelope back">
  <svg class="flap" viewBox="0 0 1000 434" aria-hidden="true">
    <path d="M0 4 L500 236 L1000 4" fill="none" stroke="#e4e8e6" stroke-width="8"/>
    <path d="M0 0 L500 230 L1000 0" fill="none" stroke="#d7ddda" stroke-width="1.2"/>
  </svg>
  <div class="seal"><span class="brand-dot"></span>Bright Harbor Dental</div>
</section>

</body>
</html>
```